Real Estate Brokerage Stationery Designs

I am looking to have presentation folders with business card slots on both sides along with pockets on both sides. I've attached logos, website colors along with current business card designs.

I am looking for envelope designs both big and small. Possibly new business card designs, notepad templates for big and small notepads. Letterhead designs. Pop socket designs. Realtors name badge designs.

www.brightholdrealty.example

```html
<!DOCTYPE html>
<html lang="en">
<head>
<meta charset="utf-8">
<title>Brighthold Realty – Business Card</title>
<link href="https://fonts.googleapis.com/css2?family=Open+Sans:wght@400;600;700&display=swap" rel="stylesheet">
<style>
  :root {
    --backdrop: #a3a3a3;
    --paper: #ffffff;
    --brand-blue: #1a5fc4;
    --brand-blue-deep: #0b4aa8;
    --brand-blue-light: #3b8ae6;
    --ink-dark: #141414;
    --ink-grey: #8a8a8a;
    --ink-body: #4a4a4a;
    --chip-grey: #cfcfcf;
  }
  * { box-sizing: border-box; margin: 0; padding: 0; }
  html, body {
    width: 1200px; height: 914px; overflow: hidden;
    background: var(--backdrop);
    font-family: "Open Sans", Arial, sans-serif;
  }
  .sheet {
    position: relative; width: 1200px; height: 914px;
    display: flex; justify-content: center; align-items: center; gap: 80px;
  }
  .card {
    position: relative; width: 340px; height: 595px;
    box-shadow: 0 18px 40px rgba(0,0,0,0.25);
  }
  /* Front side */
  .card--front {
    background: var(--paper);
    display: flex; flex-direction: column; align-items: center;
    padding-top: 34px;
  }
  .top-mark { width: 22px; height: 14px; background: var(--chip-grey); }
  .portrait {
    margin-top: 48px; width: 150px; height: 150px; border-radius: 50%;
    background: radial-gradient(circle at 50% 40%, #5a4a40 0%, #2e2a2a 60%, #1e1e22 100%);
  }
  .agent-name {
    margin-top: 22px; color: var(--brand-blue);
    font-weight: 700; font-size: 26px; letter-spacing: 0.3px;
  }
  .agent-role { color: var(--ink-grey); font-size: 16px; margin-top: 2px; }
  .contact-list {
    list-style: none; margin-top: 34px; width: 270px;
    font-size: 12.5px; color: var(--ink-body); line-height: 1.9;
  }
  .contact-list li { display: flex; align-items: flex-start; gap: 9px; }
  .contact-list .accent { color: var(--brand-blue); font-weight: 600; }
  .contact-list svg { flex: none; margin-top: 6px; }
  .phone-pair { display: flex; gap: 16px; }
  .phone-pair span { display: flex; align-items: center; gap: 7px; }
  .phone-pair svg { margin-top: 0; }

  /* Back side */
  .card--back {
    background: radial-gradient(ellipse at 50% 38%, var(--brand-blue-light) 0%, var(--brand-blue) 45%, var(--brand-blue-deep) 100%);
    display: flex; flex-direction: column; align-items: center;
  }
  .brand-name {
    margin-top: 230px; color: var(--ink-dark);
    font-weight: 700; font-size: 34px; letter-spacing: 0.5px; text-align: center; line-height: 1.1;
  }
  .divider {
    margin-top: 150px; width: 230px; height: 2px;
    background: linear-gradient(90deg, transparent, rgba(0,0,0,0.35), transparent);
  }
  .services {
    margin-top: 16px; color: #fff; font-size: 12.5px; text-align: center; line-height: 1.9;
  }
  .services .dot {
    display: inline-block; width: 6px; height: 6px; border-radius: 50%;
    background: var(--brand-blue-deep); margin: 0 6px; vertical-align: middle;
  }
  .bottom-mark { position: absolute; bottom: 26px; width: 26px; height: 14px; background: var(--chip-grey); }
</style>
</head>
<body>
<main class="sheet">
  <section class="card card--front" aria-label="Business card front">
    <div class="top-mark"></div>
    <div class="portrait" role="img" aria-label="Portrait photo of the broker"></div>
    <h1 class="agent-name">Marcus Ellery</h1>
    <p class="agent-role">Broker</p>
    <ul class="contact-list">
      <li>
        <svg width="10" height="12" viewBox="0 0 10 12"><path d="M5 0a4 4 0 0 1 4 4c0 3-4 8-4 8S1 7 1 4a4 4 0 0 1 4-4z" fill="var(--brand-blue)"/><circle cx="5" cy="4" r="1.5" fill="#fff"/></svg>
        <span class="accent">2400 Harbor Point Dr, Ste 310,<br>Lakeview, FL 33400</span>
      </li>
      <li class="phone-pair">
        <span><svg width="10" height="10" viewBox="0 0 10 10"><path d="M2 0l2 2-1 2 3 3 2-1 2 2-2 2C4 10 0 6 0 2z" fill="var(--brand-blue)"/></svg>555-013-2048</span>
        <span><svg width="10" height="10" viewBox="0 0 10 10"><rect x="2" y="0" width="6" height="10" rx="1" fill="var(--brand-blue)"/></svg>555-019-3671</span>
      </li>
      <li>
        <svg width="11" height="9" viewBox="0 0 11 9"><rect width="11" height="9" rx="1" fill="var(--brand-blue)"/><path d="M0 1l5.5 4L11 1" stroke="#fff" fill="none"/></svg>
        <span>contact@brightholdrealty.example</span>
      </li>
      <li>
        <svg width="10" height="10" viewBox="0 0 10 10"><circle cx="5" cy="5" r="5" fill="var(--brand-blue)"/></svg>
        <span>www.brightholdrealty.example</span>
      </li>
    </ul>
  </section>

  <section class="card card--back" aria-label="Business card back">
    <h2 class="brand-name">Brighthold<br>Realty</h2>
    <div class="divider"></div>
    <p class="services">
      Residential Real Estate<span class="dot"></span>Commercial Real Estate<br>
      Property Management<span class="dot"></span>Investments
    </p>
    <div class="bottom-mark"></div>
  </section>
</main>
</body>
</html>
```